BRIX Selfie Wall Design for Coworking Space

Design a striking, large-scale wall mural for BRIX Space that embodies our brand identity, incorporates Oakland-inspired elements, and enhances our coworking and event space. The design should be bold, visually engaging, and aligned with our brand aesthetic—featuring black, white, and bronze tones.
Key Requirements:
Branded Mural Design
Prominently (but tastefully) feature the BRIX Space logo.
Use abstract shapes, gradients, or geometric patterns (inspired by the BRIX logo) to convey movement and connectivity.
Incorporate the tagline: “Live · Work · Play · Go” in brand-approved typography.
Avoid literal imagery—keep the design sleek and modern.
Integrated Selfie Wall
Designate a photo-friendly zone with:
Open negative space (clean background) for people to pose naturally.
A bold but simple focal point (e.g., stylized typography, an Oakland-inspired icon, or a bronze metallic accent).
Lighting-friendly elements (avoid small patterns that may clash on camera).
Oakland Nods
Subtle references to the city (e.g., abstract skyline, bridge motifs, or topographic patterns) without being literal.
Updates
After reviewing designs, management has asked that this design incorporates a "selfie" aspect where people would be encouraged to take a photo with the wall. This would leave a thoughtful area for people to pose or engage with the design on the wall. Ideally, we want people to see the wall and take a picture with the design as a background
Target Market(s)
Office Employees
Industry/Entity Type
Real Estate/Coworking
Other font styles liked:
- Henderson Sans
Look and feel

```html
<!DOCTYPE html>
<html lang="en">
<head>
<meta charset="utf-8">
<title>BRIX Space — Live, Work, Play, Go</title>
<link href="https://fonts.googleapis.com/css2?family=Unbounded:wght@500;600;700&display=swap" rel="stylesheet">
<style>
  :root{
    --paper:#fdf4ee;
    --bronze:#7e3a1e;
    --bronze-deep:#5a2410;
    --bronze-mid:#a8592f;
    --bronze-light:#e8a670;
    --blush:#f3c9b0;
    --ink:#141414;
    --skyline:#e6cfc1;
    --line-faint:#d9c2b4;
  }
  *{margin:0;padding:0;box-sizing:border-box}
  html,body{width:1200px;height:666px;overflow:hidden;background:var(--paper)}
  .mural{position:relative;width:1200px;height:666px;background:var(--paper);overflow:hidden;font-family:"Unbounded",sans-serif}
  .brand{position:absolute;left:60px;top:57px;display:flex;align-items:center;gap:22px}
  .brand-mark{width:56px;height:56px;background:var(--bronze-mid)}
  .brand-name{font-weight:600;font-size:40px;letter-spacing:4px;color:var(--ink);line-height:1}
  .tagline{position:absolute;left:62px;top:148px;font-weight:700;font-size:76px;line-height:77px;letter-spacing:2px}
  .tagline span{display:block}
  .tagline .bronze{color:var(--bronze)}
  .tagline .ink{color:var(--ink)}
  .skyline{position:absolute;left:0;top:400px;width:536px;height:266px;
    background:linear-gradient(to bottom,rgba(230,207,193,0) 0%,var(--skyline) 55%,var(--skyline) 100%)}
  .panels{position:absolute;inset:0}
  .icon-tile{position:absolute;width:40px;height:40px;border:2px solid var(--line-faint);border-radius:6px;transform:rotate(45deg)}
  .icon-tile.one{left:366px;top:114px}
  .icon-tile.two{left:478px;top:380px;transform:rotate(30deg)}
  .icon-tile.three{left:1114px;top:206px;transform:none;border-radius:10px}
</style>
</head>
<body>
<main class="mural">
  <div class="skyline" role="img" aria-label="Soft bronze skyline of the city with bridge, towers and trees"></div>

  <svg class="panels" width="1200" height="666" viewBox="0 0 1200 666" aria-hidden="false">
    <defs>
      <linearGradient id="bronzeSweep" x1="0" y1="0" x2="1" y2="0">
        <stop offset="0" stop-color="#8a3e1f"/>
        <stop offset="1" stop-color="#e8a670"/>
      </linearGradient>
      <linearGradient id="workTone" x1="0" y1="0" x2="1" y2="1">
        <stop offset="0" stop-color="#f6d4c0"/>
        <stop offset="0.6" stop-color="#d99272"/>
        <stop offset="1" stop-color="#6a2c14"/>
      </linearGradient>
      <linearGradient id="playTone" x1="0" y1="0" x2="1" y2="1">
        <stop offset="0" stop-color="#7a3518"/>
        <stop offset="0.45" stop-color="#d98f68"/>
        <stop offset="1" stop-color="#4e1e0c"/>
      </linearGradient>
    </defs>
    <polygon points="661,0 1192,0 1062,203 787,203" fill="url(#bronzeSweep)" role="img" aria-label="Motorcycle rider over a city skyline"/>
    <polygon points="630,16 894,433 631,433 503,218" fill="url(#workTone)" role="img" aria-label="City construction scene with cranes and towers"/>
    <polygon points="810,233 1071,233 1200,450 1067,650" fill="url(#playTone)" role="img" aria-label="Forest landscape in motion"/>
    <polygon points="637,463 911,463 1043,666 512,666" fill="url(#bronzeSweep)" role="img" aria-label="Farmer holding a crate of fresh produce"/>
    <text x="661" y="518" font-family="Unbounded, sans-serif" font-weight="500" font-size="66" fill="none" stroke="#f3c9b0" stroke-opacity="0.55" stroke-width="1" letter-spacing="4">LIVE</text>
    <text x="790" y="140" font-family="Unbounded, sans-serif" font-weight="500" font-size="120" fill="none" stroke="#f3c9b0" stroke-opacity="0.4" stroke-width="1">GO</text>
  </svg>

  <div class="icon-tile one"></div>
  <div class="icon-tile two"></div>
  <div class="icon-tile three"></div>

  <header class="brand">
    <div class="brand-mark"></div>
    <span class="brand-name">BRIX</span>
  </header>

  <h1 class="tagline">
    <span class="bronze">LIVE,</span>
    <span class="ink">WORK,</span>
    <span class="bronze">PLAY,</span>
    <span class="ink">GO</span>
  </h1>
</main>
</body>
</html>
```